Web Developer Wordpress theme

I'm a web developer but a poor designer so i need somebody to design me a cool and professional WordPress theme. I specialize in shopping cart developments and modifications as well as hosting for these system so would like the design to show this off. I am UK based and want this to also come across in the design.
As for colors and layout i am open mined just use your imaginantion i will let know what i think of your designs.
also forgot to mention my business name is valtrique
and my exsiting site is valtrique.co.uk

```html
<!DOCTYPE html>
<html lang="en">
<head>
<meta charset="utf-8">
<title>valtrique – serious web development</title>
<link rel="stylesheet" href="https://fonts.googleapis.com/css2?family=Source+Sans+3:ital,wght@0,400;0,600;1,700&family=Quicksand:wght@500&display=swap">
<style>
:root{
  --night:#1c1c1d;
  --night-deep:#121213;
  --mist:#d9d9dd;
  --panel:#f2f2f4;
  --panel-low:#c6c6cb;
  --ember:#f28a0c;
  --link:#1d6fc2;
  --ink:#1f1f1f;
  --paper:#ffffff;
  --chrome:#e8e8ea;
}
*{box-sizing:border-box;margin:0;padding:0}
html,body{width:1200px;height:1099px;overflow:hidden}
body{position:relative;background:var(--mist);font-family:"Source Sans 3",Arial,sans-serif;color:var(--ink)}
.stage{position:absolute;left:0;top:0;width:1200px;height:588px;background:linear-gradient(180deg,#202021,var(--night-deep))}
.brand-plate{position:absolute;left:48px;top:-6px;width:382px;height:134px;background:linear-gradient(#f3f3f4,#d7d7da);border-radius:0 0 14px 14px;box-shadow:0 2px 6px rgba(0,0,0,.6)}
.brand-plate::after{content:"";position:absolute;inset:6px 6px 6px 6px;border:1.5px dashed #8c8c90;border-radius:0 0 10px 10px}
.brand-name{position:absolute;left:28px;top:22px;font-size:58px;font-weight:600;color:var(--ember);letter-spacing:-1px;line-height:1}
.brand-tag{position:absolute;left:112px;top:92px;font-family:"Quicksand",sans-serif;font-size:13px;letter-spacing:2.3px;color:#555}
.social{position:absolute;top:9px;left:1028px;display:flex;gap:5px}
.social span{width:34px;height:34px;border-radius:3px;background:linear-gradient(#4d8fd6,#1e5da8)}
.main-nav{position:absolute;left:520px;top:83px;width:632px;height:43px;border-radius:8px;background:linear-gradient(#6b6b6e,#3b3b3d 50%,#252527);border:1px solid #111;display:flex;align-items:center;padding-left:24px;gap:0}
.main-nav a{color:#f2f2f2;text-decoration:none;font-size:21px;margin-right:30px}
.slide-art{position:absolute;left:54px;top:150px;width:600px;height:318px;background:radial-gradient(ellipse at 45% 45%,#5a5f68,#2a2c30 60%,transparent 80%)}
.slide-arrow{position:absolute;top:288px;width:40px;height:40px;border-radius:50%;background:linear-gradient(#6a6a6c,#2a2a2b);border:2px solid #9a9a9c}
.slide-arrow svg{position:absolute;left:12px;top:11px}
.slide-copy{position:absolute;left:696px;top:236px;width:454px}
.slide-copy h1{font-weight:400;font-size:34px;color:var(--ember);margin:0 0 10px 2px}
.slide-copy p{font-size:18px;line-height:28.8px;color:#ececec;text-align:justify}
.feature{position:absolute;top:470px;width:228px;height:228px;border-radius:50%;background:radial-gradient(circle,#f6f6f7 60%,#bdbdc1);box-shadow:0 2px 5px rgba(0,0,0,.3)}
.feature-core{position:absolute;left:14px;top:14px;width:200px;height:200px;border-radius:50%;background:radial-gradient(circle at 50% 40%,#2c2c2e,#141415);border:4px solid #4a4a4c}
.feature-core::after{content:"";position:absolute;inset:7px;border-radius:50%;border:2px dashed #8a8a8c}
.feature-title{position:absolute;left:0;right:0;text-align:center;color:var(--paper);font-family:"Quicksand",sans-serif;font-size:23px;letter-spacing:2.5px;line-height:28px}
.feature-icon{position:absolute;left:82px;width:40px;height:36px;border-radius:6px}
.panel{position:absolute;top:734px;width:352px;height:252px;border-radius:6px;background:linear-gradient(var(--panel) 45%,var(--panel-low));box-shadow:0 1px 5px rgba(0,0,0,.35)}
.panel-tab{position:absolute;left:12px;top:-10px;width:148px;height:46px;border-radius:6px 6px 10px 10px;background:linear-gradient(#ffffff,#e4e4e7);box-shadow:0 2px 3px rgba(0,0,0,.3);font-size:21px;padding:12px 0 0 23px;color:#2a2a2a}
.blog-entry{position:absolute;left:26px;width:294px;font-size:15.6px;line-height:21.6px;text-align:justify}
.blog-entry h3{font-style:italic;font-weight:700;font-size:15px;color:var(--link);margin-bottom:1px}
.service{position:absolute;left:10px;width:314px;display:flex;gap:8px;font-size:15px;line-height:21.6px;text-align:justify}
.service-icon{flex:none;width:48px;height:44px;margin-top:4px;border-radius:4px}
.field{position:absolute;left:28px;width:290px;height:36px;border-radius:8px;background:var(--paper);font-size:16px;color:#777;padding:7px 16px}
.send{position:absolute;left:186px;top:210px;width:122px;height:30px;border-radius:15px;background:linear-gradient(#5a5a5c,#111);border:1px solid #000;color:var(--paper);font-size:21px;text-align:center;line-height:27px}
.site-foot{position:absolute;left:0;top:1042px;width:1200px;height:57px;background:var(--night);color:#e6e6e6;font-size:13px;text-align:center;line-height:73px}
</style>
</head>
<body>
<div class="stage"></div>

<header>
  <div class="brand-plate">
    <div class="brand-name">valtrique</div>
    <div class="brand-tag">serious web developement</div>
  </div>
  <div class="social" aria-label="Social profiles"><span></span><span></span><span></span></div>
  <nav class="main-nav">
    <a href="#">Home</a><a href="#">About Us</a><a href="#">Services</a><a href="#">Addons</a><a href="#">Contact</a><a href="#">Blog</a>
  </nav>
</header>

<section class="hero">
  <div class="slide-art" role="img" aria-label="Developer in a suit standing beside a row of website screenshots"></div>
  <div class="slide-arrow" style="left:7px"><svg width="14" height="16"><path d="M12 1 L2 8 L12 15Z" fill="#fff"/></svg></div>
  <div class="slide-arrow" style="left:1157px"><svg width="14" height="16"><path d="M3 1 L13 8 L3 15Z" fill="#fff"/></svg></div>
  <div class="slide-copy">
    <h1>UK Freelance Web Developer</h1>
    <p>Freelance web developer avaliable for hire, Specializing in Stallcart shopping cart and creating addons and customized templates. I have been a freelance developer for over 5 years now and complete all sizes of projects starting out on Hire-a-Maker doing small project then going on to the larger projects.</p>
  </div>
</section>

<section class="features">
  <div class="feature" style="left:122px">
    <div class="feature-core">
      <div class="feature-title" style="top:60px">Stallcart<br>Addons</div>
      <div class="feature-icon" role="img" aria-label="Puzzle piece icon" style="top:128px;background:linear-gradient(#d6d6d8,#8c8c90)"></div>
    </div>
  </div>
  <div class="feature" style="left:474px">
    <div class="feature-core">
      <div class="feature-title" style="top:52px">Stallcart<br>Template</div>
      <div class="feature-icon" role="img" aria-label="Photo prints icon" style="top:122px;background:linear-gradient(#e9eef5,#7d93b3)"></div>
    </div>
  </div>
  <div class="feature" style="left:856px">
    <div class="feature-core">
      <div class="feature-title" style="top:40px">Shopping<br>Cart<br>Software</div>
      <div class="feature-icon" role="img" aria-label="Shopping basket icon" style="top:138px;background:linear-gradient(#d99a5a,#93531f)"></div>
    </div>
  </div>
</section>

<section class="panel" style="left:56px">
  <div class="panel-tab">From Blog</div>
  <article class="blog-entry" style="top:50px"><h3>Lorem Ipsum</h3>Lorem Ipsum is simply dummy text of the printing and typesetting industry</article>
  <article class="blog-entry" style="top:130px"><h3>Lorem Ipsum</h3>Lorem Ipsum is simply dummy text of the printing and typesetting industry</article>
</section>

<section class="panel" style="left:428px">
  <div class="panel-tab">Our Services</div>
  <div class="service" style="top:56px"><div class="service-icon" role="img" aria-label="Payment card icon" style="background:linear-gradient(#8ec9a0,#3d7f55)"></div><p>Fast and Secure web hosting Servers to support your e-commerce solution</p></div>
  <div class="service" style="top:104px"><div class="service-icon" role="img" aria-label="Cash register icon" style="background:linear-gradient(#8ca0b8,#2f3a48)"></div><p>Specialize in shopping cart solutions and customizing them to meet your needs</p></div>
  <div class="service" style="top:174px"><div class="service-icon" role="img" aria-label="Design tools icon" style="background:linear-gradient(#9fc2ec,#4a6fa8)"></div><p>Design your online store to make it comfortable and easy for your custom-ers to browser and purchase</p></div>
</section>

<section class="panel" style="left:798px">
  <div class="panel-tab" style="width:202px">Quick Contact</div>
  <div class="field" style="top:48px">Name</div>
  <div class="field" style="top:94px">Email</div>
  <div class="field" style="top:138px;height:60px">Message</div>
  <div class="send">Submit</div>
</section>

<footer class="site-foot">Copyright © 2012. www. valtrique.com</footer>
</body>
</html>
```